Harborline Renewal Business Card Design

Professional and clean design. The design colors should flow with the logo. Two-sided card with the website on the back which is:

www.HarborlineRenewal.example.

"Specializing in Water Damage Restoration"

On the front I need the name, email, phone, and logo.

Name: Darnell Quisby
Email: Darnell@HarborlineRenewal.example
Phone: 555-318-2046 for now

I only have the Preview and Thumbnail right now but should have the source files uploaded within a day or two.

Target Market(s)

Flood victims, home owners with water damage from busted pipes etc...

Industry/Entity Type

Business

Contact Information for Business Card

Name: Darnell Quisby

Font styles to use
Serif
Sans Serif

Requirements
Must have
• Business Card Details Info

```html
<!DOCTYPE html>
<html lang="en">
<head>
<meta charset="utf-8">
<title>Harborline Renewal Business Card</title>
<link rel="stylesheet" href="https://fonts.googleapis.com/css2?family=Cinzel:wght@400;600&family=Open+Sans:wght@400&display=swap">
<style>
  :root {
    --page: #eceae6;
    --card: #ffffff;
    --blue-deep: #2a8fd2;
    --blue-sky: #5bc0ee;
    --ink: #2b2b2b;
    --ink-soft: #444444;
    --edge: #3a3a3a;
  }
  * { margin: 0; padding: 0; box-sizing: border-box; }
  html, body {
    width: 1200px; height: 1188px; overflow: hidden;
    background: var(--page);
  }
  .canvas { position: relative; width: 1200px; height: 1188px; }

  .card {
    position: absolute;
    background: var(--card);
    border-radius: 50px;
    overflow: hidden;
    box-shadow: 0 2px 8px rgba(0,0,0,0.12);
  }
  .card--front { left: 233px; top: 77px; width: 907px; height: 521px; }
  .card--back  { left: 37px; top: 626px; width: 909px; height: 517px; border: 1.5px solid var(--edge); }

  .brand-dot {
    position: absolute; left: 50%; width: 124px; height: 124px;
    margin-left: -62px; border-radius: 50%;
    background: var(--blue-sky);
  }
  .card--front .brand-dot { top: 17px; }
  .card--back .brand-dot { top: 84px; }

  .brand-name {
    position: absolute; left: 0; width: 100%; text-align: center;
    font-family: "Cinzel", serif; font-weight: 600;
    font-size: 50px; letter-spacing: 2px;
    color: var(--blue-deep); white-space: nowrap;
  }
  .card--front .brand-name { top: 178px; }
  .card--back .brand-name { top: 262px; }

  .holder {
    position: absolute; top: 280px; left: 0; width: 100%; text-align: center;
    font-family: "Cinzel", serif; font-weight: 600; font-size: 27px;
    letter-spacing: 1px; color: var(--blue-deep);
  }
  .holder__title { color: var(--ink-soft); font-weight: 400; }

  .wave { position: absolute; left: 0; top: 0; }

  .contact {
    position: absolute; left: 0; width: 100%; text-align: center;
    font-family: "Open Sans", sans-serif; font-size: 20px; color: var(--ink);
    display: flex; justify-content: center; align-items: center; gap: 10px;
  }
  .contact--phone { top: 386px; }
  .contact--online { top: 421px; }
  .contact__item { display: inline-flex; align-items: center; gap: 8px; }
  .contact__item + .contact__item { margin-left: 12px; }
  .contact svg { width: 18px; height: 18px; }

  .tagline {
    position: absolute; top: 462px; left: 0; width: 100%; text-align: center;
    font-family: "Cinzel", serif; font-size: 24px; letter-spacing: 1px;
    color: var(--ink-soft);
  }

  .website {
    position: absolute; top: 383px; left: 0; width: 100%; text-align: center;
    font-family: "Open Sans", sans-serif; font-size: 27px; letter-spacing: 2px;
    color: var(--ink);
  }
</style>
</head>
<body>
<main class="canvas">

  <section class="card card--front" aria-label="Card front">
    <svg class="wave" width="907" height="521" viewBox="0 0 907 521" aria-hidden="true">
      <path d="M0,425 Q453,250 907,425 L907,521 L0,521 Z" fill="var(--blue-sky)"/>
      <path d="M0,410 Q453,224 907,410" fill="none" stroke="var(--blue-deep)" stroke-width="5"/>
    </svg>
    <div class="brand-dot" aria-hidden="true"></div>
    <h1 class="brand-name">Harborline Renewal</h1>
    <p class="holder">Darnell Quisby, <span class="holder__title">Title</span></p>

    <p class="contact contact--phone">
      <span class="contact__item">
        <svg viewBox="0 0 20 20" aria-hidden="true"><circle cx="10" cy="10" r="9" fill="none" stroke="var(--ink)" stroke-width="1.5"/><path d="M6.5 5.5 L8.5 5 L9.5 7.5 L8.3 8.5 Q9.3 10.8 11.5 11.7 L12.5 10.5 L15 11.5 L14.5 13.5 Q8 14 6.5 5.5 Z" fill="var(--ink)"/></svg>
        555-318-2046
      </span>
    </p>
    <p class="contact contact--online">
      <span class="contact__item">
        <svg viewBox="0 0 20 20" aria-hidden="true"><rect x="2" y="5" width="16" height="11" fill="var(--ink)"/><path d="M2 5 L10 11 L18 5" fill="none" stroke="#fff" stroke-width="1.4"/></svg>
        Darnell@HarborlineRenewal.example
      </span>
      <span class="contact__item">
        <svg viewBox="0 0 20 20" aria-hidden="true"><g fill="none" stroke="var(--ink)" stroke-width="1.4"><circle cx="10" cy="10" r="8"/><ellipse cx="10" cy="10" rx="3.5" ry="8"/><path d="M2 10 H18 M3.5 6 H16.5 M3.5 14 H16.5"/></g></svg>
        www.HarborlineRenewal.example
      </span>
    </p>
    <p class="tagline">Specializing in Water Damage Restoration</p>
  </section>

  <section class="card card--back" aria-label="Card back">
    <div class="brand-dot" aria-hidden="true"></div>
    <h2 class="brand-name">Harborline Renewal</h2>
    <p class="website">www.HarborlineRenewal.example</p>
  </section>

</main>
</body>
</html>
```